Velkora Land Surveying Website Design

We are working with Velkora. They are a national land surveying company and in need of a new website design.

Some sites to use for inspiration:

https://brannickeng.com
https://www.dvwinc.com
https://kelvarin.com
https://gto.us
https://ravendobuilt.com
https://www.marbeckquillondale.com

Thank you for taking the time to consider designing a website for us. We are web developers based in Stockton and Los Angeles, CA, USA. Most of our projects go through the same process. Understanding this process may help you win a project with us. We custom-code all of our websites in-house. We don’t have any requirements as to what tools you use for your design, but we prefer Figma files. For any design that we label as four-stars, we send it to the client for review. The client picks the final design they want us to use. Once we complete this process, we will continue to show additional clients all the four-star sites and purchase them later. Your designs will have multiple chances to sell. For better chances of success, we ask that you follow these guidelines.

IMAGES:
If you use any images or icons in the design, we ask that you have a link to the asset so we can purchase the image/icon. Most of the designs we submit do not have the customer’s images on them unless they have some great images. Be creative; show us the feeling you are trying to portray with your image choices. Use any royalty-free site you choose. We subscribe to Pellix and mainly use their images, but we can purchase images outside of Pellix.

PLEASE NOTE: we will not submit designs to clients with watermarks on the images.

FONTS:
We ask that you identify the fonts used in the design. This can be done in a message if you want. We typically use Google Fonts and Pellix Fonts.

CONTENT:
We're always open to different content and ideas. We often submit designs with stock images so the client can see our vision. We typically take pictures after the website launch to use their images with our vision. Lorem Ipsum is fine for paragraphs, but we ask that you write the headers in correct English. We want to be able to show the vision and identify the sections of the website.

INSPIRATION:
We typically add a couple of links in the brief of websites we like to help you get started in your design.

REVISIONS:
We do not often ask for revisions of the designs unless we see something in the design that may not appeal to the client. If there are slight changes that we want to make, we do that in the development process.

FEEDBACK:
We rarely give feedback on designs during the design process. We are working on many website projects and do not have the time to provide feedback. We usually respond if your request is well thought out and asks specific questions, but a note asking “feedback, please” usually goes unanswered.

```html
<!DOCTYPE html>
<html lang="en">
<head>
<meta charset="utf-8">
<title>Velkora Land Surveying</title>
<link rel="stylesheet" href="https://fonts.googleapis.com/css2?family=Oswald:wght@300;400;500;600;700&family=Mulish:wght@400;600;700;800&family=Poppins:wght@500;600&display=swap">
<style>
:root{
  --red:#e2463a;
  --red-dark:#c9372c;
  --grey:#767676;
  --grey-band:#7b7b7b;
  --ink:#161616;
  --text:#4a4a4a;
  --paper:#ffffff;
  --mist:#f5f3f3;
}
*{box-sizing:border-box;margin:0;padding:0}
html,body{width:1200px;height:3592px;overflow:hidden}
body{position:relative;background:var(--paper);font-family:"Mulish",sans-serif;color:var(--text)}
.head{font-family:"Oswald",sans-serif;text-transform:uppercase;color:var(--ink)}
.accent{color:var(--red)}
.btn{position:absolute;display:flex;align-items:center;justify-content:center;background:var(--red);color:#fff;font-family:"Oswald",sans-serif;font-weight:600;text-transform:uppercase}
section{position:absolute;left:0;width:1200px}
.abs{position:absolute}

/* hero */
.hero{top:0;height:661px;background:linear-gradient(160deg,#3f4c3e 0%,#2f3b2f 40%,#3d4636 70%,#2a3328 100%)}
.hero-photo{position:absolute;inset:0;background:radial-gradient(ellipse at 75% 20%,rgba(120,125,115,.45),transparent 55%),radial-gradient(ellipse at 20% 70%,rgba(70,95,60,.5),transparent 60%)}
.hero-shade{position:absolute;inset:0;background:rgba(0,0,0,.35)}
.brand{position:absolute;left:151px;top:36px;display:flex;align-items:center;gap:12px}
.brand-dot{width:52px;height:52px;border-radius:50%;background:var(--red)}
.brand-name{font-family:"Oswald",sans-serif;font-weight:600;font-size:34px;line-height:1;color:var(--red);letter-spacing:1px}
.nav a{position:absolute;top:31px;height:42px;display:flex;align-items:center;font-family:"Oswald",sans-serif;font-size:17px;color:#fff;text-decoration:none;text-transform:uppercase}
.nav .current{border:2px solid #fff;padding:0 12px}
.nav .cta{background:var(--red);padding:0 20px}
.hero-title{position:absolute;top:182px;width:100%;text-align:center;font-family:"Oswald",sans-serif;font-weight:700;font-size:70px;line-height:58px;color:#fff;text-transform:uppercase}
.hero-lede{position:absolute;top:380px;width:100%;text-align:center;color:#fff;font-size:21px;line-height:31px}
.hero-lede b{color:var(--red);font-weight:800}
.dots span{position:absolute;left:1106px;width:11px;height:11px;border-radius:50%;border:1.5px solid #fff}
.dots .on{background:#fff}

/* services */
.services{top:661px;height:646px;background:#fbfbfb}
.sec-title{position:absolute;width:100%;text-align:center;font-size:42px;font-weight:600;top:40px}
.rule{position:absolute;height:3px;width:44px;background:var(--ink)}
.card{position:absolute;width:289px;height:206px;background:#fff;box-shadow:0 4px 16px rgba(0,0,0,.07)}
.card svg{position:absolute;left:43px;top:24px}
.card h3{position:absolute;left:88px;top:33px;font-size:19px;font-weight:500;font-family:"Oswald",sans-serif;color:var(--ink);text-transform:uppercase;white-space:nowrap}
.card p{position:absolute;left:43px;top:80px;width:205px;font-size:12px;line-height:16.5px}
.card .btn{left:43px;top:150px;width:78px;height:27px;font-size:11px}
.card.featured{background:var(--red)}
.card.featured h3,.card.featured p{color:#fff}
.card.featured .btn{background:#8c8c8c}

/* welcome */
.welcome{top:1307px;height:504px}
.welcome-copy{position:absolute;left:0;top:0;width:540px;height:504px;background:var(--grey);color:#fff}
.fields{position:absolute;left:540px;top:0;width:660px;height:504px;background:linear-gradient(150deg,#7d9c4a 0%,#4e8a38 30%,#b59a5a 55%,#5d9440 75%,#a48450 100%)}
.welcome-copy .eyebrow{position:absolute;left:145px;top:60px;font-family:"Oswald",sans-serif;font-weight:300;font-size:33px;line-height:40px;text-transform:uppercase;white-space:nowrap}
.welcome-copy .badge-name{position:absolute;left:145px;top:109px;height:63px;padding:0 8px;background:var(--red);font-family:"Oswald",sans-serif;font-weight:700;font-size:60px;line-height:63px;text-transform:uppercase}
.welcome-copy .welcome-sub{position:absolute;left:145px;top:192px;font-family:"Oswald",sans-serif;font-weight:500;font-size:22px;line-height:29px;text-transform:uppercase;white-space:nowrap}
.welcome-copy .welcome-text{position:absolute;left:146px;top:268px;width:345px;font-size:13.5px;line-height:19px}

/* stats + why */
.why{top:1811px;height:746px}
.station{position:absolute;left:0;top:0;width:540px;height:746px;background:linear-gradient(170deg,#8d7261 0%,#a17e66 35%,#8a6c5c 70%,#7d6355 100%)}
.stats{position:absolute;left:540px;top:0;width:660px;height:138px;background:var(--grey-band);color:#fff}
.stat{position:absolute;top:30px}
.stat b{display:block;font-family:"Oswald",sans-serif;font-weight:500;font-size:33px;line-height:38px}
.stat span{font-size:13.5px}
.stat-div{position:absolute;top:42px;width:3px;height:48px;background:var(--red)}
.why-title{position:absolute;left:586px;top:187px;font-size:41px;font-weight:600}
.mark-circle{position:absolute;left:865px;top:177px;width:78px;height:78px;border-radius:50%;background:var(--red)}
.col-div{position:absolute;left:824px;top:278px;width:2px;height:442px;background:#555}
.reason svg{position:absolute}
.reason h5{position:absolute;font-family:"Oswald",sans-serif;font-weight:500;font-size:21px;line-height:29px;color:var(--ink);text-transform:uppercase}
.reason p{position:absolute;width:192px;font-size:12.5px;line-height:16.5px}

/* projects */
.projects{top:2557px;height:550px}
.projects-copy{position:absolute;left:0;top:0;width:544px;height:550px;background:var(--mist)}
.creek{position:absolute;left:544px;top:0;width:656px;height:550px;background:radial-gradient(ellipse at 40% 45%,#6b8a3a,transparent 60%),linear-gradient(135deg,#8a9a45 0%,#5d7a33 40%,#a08a40 65%,#4f6f2e 100%)}
.projects h2{position:absolute;left:151px;top:56px;font-size:41px;font-weight:600}
.projects-copy .projects-text{position:absolute;left:153px;top:171px;width:345px;font-size:13.5px;line-height:19px}
.question{position:absolute;left:155px;top:308px;width:338px;height:101px;background:var(--grey);color:#fff}
.question svg{position:absolute;left:30px;top:26px}
.question small{position:absolute;left:108px;top:22px;font-family:"Oswald",sans-serif;font-weight:500;font-size:17px}
.question strong{position:absolute;left:102px;top:46px;font-family:"Oswald",sans-serif;font-weight:500;font-size:30px}

/* footer */
.footer{position:absolute;left:0;top:3107px;width:1200px;height:485px;background:var(--red);color:#fff}
.cta-strip{position:absolute;left:148px;top:49px;width:901px;height:87px;background:#fff}
.cta-strip h2{position:absolute;left:28px;top:16px;font-family:"Oswald",sans-serif;font-weight:600;font-size:40px;color:var(--red);text-transform:uppercase}
.cta-strip a{position:absolute;left:698px;top:20px;width:180px;height:47px;border:2px solid var(--red);display:flex;align-items:center;justify-content:center;gap:10px;font-family:"Oswald",sans-serif;font-weight:500;font-size:20px;color:var(--red);text-decoration:none;text-transform:uppercase}
.footer-mark{position:absolute;left:170px;top:198px;width:230px;height:230px;border-radius:50%;border:6px solid #fff;display:flex;align-items:center;justify-content:center;font-family:"Oswald",sans-serif;font-weight:600;font-size:40px}
.footer h6{position:absolute;top:170px;font-family:"Poppins",sans-serif;font-weight:600;font-size:22px}
.contact-line{position:absolute;left:500px;display:flex;gap:10px;font-size:12px;line-height:18px;font-weight:600}
.menu{position:absolute;left:745px;top:230px;list-style:none;font-size:12px;line-height:18px;font-weight:600}
.social span{position:absolute;top:3341px;width:29px;height:29px;border-radius:50%;border:2px solid #fff}
.quote{position:absolute;left:875px;top:302px;width:174px;height:44px;border-radius:22px;background:#fff;color:var(--red);display:flex;align-items:center;justify-content:center;font-family:"Poppins",sans-serif;font-weight:600;font-size:14px}
.footer hr{position:absolute;left:490px;top:401px;width:559px;border:0;border-top:1.5px solid #fff}
.copyright{position:absolute;right:148px;top:437px;font-size:12px;font-weight:600}
</style>
</head>
<body>

<section class="hero">
  <div class="hero-photo" role="img" aria-label="Aerial photograph of a suburban neighbourhood and roads"></div>
  <div class="hero-shade"></div>
  <div class="brand">
    <span class="brand-dot"></span>
    <span class="brand-name">VELKORA</span>
  </div>
  <nav class="nav">
    <a class="current" style="left:483px">Home</a>
    <a style="left:566px">About us</a>
    <a style="left:661px">Services</a>
    <a style="left:755px">Projects</a>
    <a style="left:848px">Careers</a>
    <a class="cta" style="left:932px">Contact us</a>
  </nav>
  <h1 class="hero-title">Precision<br><span class="accent">Land Surveying,</span><br>Nationwide</h1>
  <p class="hero-lede">Trusted <b>experts delivering accurate</b> surveying<br>solutions across the country</p>
  <a class="btn" style="left:477px;top:472px;width:246px;height:64px;font-size:25px;font-weight:500">Get a free quote</a>
  <div class="dots">
    <span class="on" style="top:270px"></span><span style="top:294px"></span><span style="top:317px"></span><span style="top:341px"></span><span style="top:366px"></span>
  </div>
</section>

<section class="services">
  <h2 class="head sec-title">Our <span class="accent">Services</span></h2>
  <div class="rule" style="left:578px;top:112px"></div>

  <article class="card" style="left:152px;top:158px">
    <svg width="36" height="44" viewBox="0 0 36 44" fill="none" stroke="#e2463a" stroke-width="2"><rect x="10" y="2" width="16" height="14"/><path d="M18 16v6M6 42l12-20 12 20M18 22v20M4 22h28"/></svg>
    <h3>Land Surveying</h3>
    <p>Lorem ipsum dolor sit amet, consec tetur adipiscing elit, sed do eiusmod tempor incididunt ut labore.</p>
    <a class="btn">Read more</a>
  </article>
  <article class="card featured" style="left:456px;top:158px">
    <svg width="38" height="40" viewBox="0 0 38 40" fill="none" stroke="#fff" stroke-width="2"><circle cx="19" cy="20" r="8"/><path d="M19 2v6M19 32v6M2 20h6M30 20h6M7 8l4 4M27 28l4 4M31 8l-4 4M11 28l-4 4"/></svg>
    <h3>Civil Engineering</h3>
    <p>Lorem ipsum dolor sit amet, consec tetur adipiscing elit, sed do eiusmod tempor incididunt ut labore.</p>
    <a class="btn">Read more</a>
  </article>
  <article class="card" style="left:760px;top:158px">
    <svg width="36" height="42" viewBox="0 0 36 42" fill="none" stroke="#e2463a" stroke-width="2"><rect x="4" y="8" width="20" height="32"/><path d="M24 18h8v22M10 14h8M10 20h8M10 26h8M10 32h8M2 40h32M30 2v6"/></svg>
    <h3>Measured Buildings</h3>
    <p>Lorem ipsum dolor sit amet, consec tetur adipiscing elit, sed do eiusmod tempor incididunt ut labore.</p>
    <a class="btn">Read more</a>
  </article>
  <article class="card" style="left:152px;top:381px">
    <svg width="40" height="42" viewBox="0 0 40 42" fill="none" stroke="#e2463a" stroke-width="2"><circle cx="20" cy="14" r="6"/><path d="M8 40c0-8 5-13 12-13s12 5 12 13M28 6l4-4M34 12h4"/></svg>
    <h3 style="left:94px">Site Engineering</h3>
    <p>Lorem ipsum dolor sit amet, consec tetur adipiscing elit, sed do eiusmod tempor incididunt ut labore.</p>
    <a class="btn">Read more</a>
  </article>
  <article class="card" style="left:456px;top:381px">
    <svg style="left:26px" width="38" height="40" viewBox="0 0 38 40" fill="none" stroke="#e2463a" stroke-width="2"><rect x="9" y="12" width="20" height="18"/><path d="M14 12V6h10v6M14 20h10M4 36h30M19 30v6"/></svg>
    <h3 style="left:72px">Development Services</h3>
    <p style="left:31px">Lorem ipsum dolor sit amet, consec tetur adipiscing elit, sed do eiusmod tempor incididunt ut labore.</p>
    <a class="btn" style="left:31px">Read more</a>
  </article>
  <article class="card" style="left:760px;top:381px">
    <svg width="38" height="40" viewBox="0 0 38 40" fill="none" stroke="#e2463a" stroke-width="2.5"><circle cx="19" cy="20" r="15"/><path d="M4 20h30M19 5c-6 5-6 25 0 30M19 5c6 5 6 25 0 30"/></svg>
    <h3>GIS &amp; Mapping</h3>
    <p>Lorem ipsum dolor sit amet, consec tetur adipiscing elit, sed do eiusmod tempor incididunt ut labore.</p>
    <a class="btn">Read more</a>
  </article>
</section>

<section class="welcome">
  <div class="welcome-copy">
    <div class="eyebrow">Welcome to</div>
    <div class="badge-name">Velkora</div>
    <h4 class="welcome-sub">Over 25 years of trusted general<br>contracting across California</h4>
    <p class="welcome-text">Sed ut perspiciatis unde omnis iste natus error sit voluptatem accusantium doloremque laudantium, totam rem aperiam, eaque ipsa quae ab illo inventore veritatis et quasi architecto beatae vitae dicta sunt explicabo. Nemo enim ipsam voluptatem quia voluptas sit aspernatur aut odit .</p>
    <a class="btn" style="left:151px;top:408px;width:113px;height:39px;font-size:18px;font-weight:500">Read more</a>
  </div>
  <div class="fields" role="img" aria-label="Aerial photograph of patchwork farm fields"></div>
</section>

<section class="why">
  <div class="station" role="img" aria-label="Surveying total station on a yellow tripod above desert canyon terrain"></div>
  <div class="stats">
    <div class="stat" style="left:42px"><b>140+</b><span>Successful Projects</span></div>
    <div class="stat-div" style="left:194px"></div>
    <div class="stat" style="left:234px"><b>38+</b><span>Team Members</span></div>
    <div class="stat-div" style="left:373px"></div>
    <div class="stat" style="left:418px"><b>80+</b><span>Happy Clients</span></div>
  </div>
  <h2 class="head why-title">Why <span class="accent">Choose Us</span></h2>
  <span class="mark-circle"></span>
  <div class="rule" style="left:586px;top:254px"></div>
  <div class="col-div"></div>

  <div class="reason">
    <svg style="left:594px;top:304px" width="42" height="36" viewBox="0 0 42 36" fill="none" stroke="#e2463a" stroke-width="2"><rect x="2" y="8" width="38" height="26"/><path d="M15 8V3h12v5M2 18h38M18 18v4h6v-4"/></svg>
    <h5 style="left:594px;top:364px">Experience</h5>
    <p style="left:595px;top:407px">Lorem ipsum dolor sit amet, consec tetur adipiscing elit, sed do eiusmod tempor incididunt ut labore.</p>

    <svg style="left:876px;top:300px" width="38" height="42" viewBox="0 0 38 42" fill="none" stroke="#e2463a" stroke-width="2"><circle cx="19" cy="13" r="8"/><path d="M9 13a10 10 0 0 1 20 0M4 40c0-9 6-14 15-14s15 5 15 14"/></svg>
    <h5 style="left:875px;top:364px">Support</h5>
    <p style="left:876px;top:407px">Lorem ipsum dolor sit amet, consec tetur adipiscing elit, sed do eiusmod tempor incididunt ut labore.</p>

    <svg style="left:594px;top:510px" width="42" height="40" viewBox="0 0 42 40" fill="none" stroke="#e2463a" stroke-width="2"><circle cx="21" cy="18" r="6"/><path d="M11 38c0-6 4-10 10-10s10 4 10 10M6 8l2 2M36 8l-2 2M21 2v4"/></svg>
    <h5 style="left:594px;top:575px">Client Success</h5>
    <p style="left:595px;top:618px">Lorem ipsum dolor sit amet, consec tetur adipiscing elit, sed do eiusmod tempor incididunt ut labore.</p>

    <svg style="left:872px;top:510px" width="42" height="42" viewBox="0 0 42 42" fill="none" stroke="#e2463a" stroke-width="2"><path d="M8 40V4M2 8h38M8 4l8 4M36 8v10M30 18h12v8H30zM2 40h14"/></svg>
    <h5 style="left:875px;top:575px">Purpose Driven<br>Construction</h5>
    <p style="left:876px;top:641px">Lorem ipsum dolor sit amet, consec tetur adipiscing elit, sed do eiusmod tempor incididunt ut labore.</p>
  </div>
</section>

<section class="projects">
  <div class="projects-copy">
    <h2 class="head">Our <span class="accent">Projects</span></h2>
    <div class="rule" style="left:151px;top:123px"></div>
    <p class="projects-text">Sed ut perspiciatis unde omnis iste natus error sit voluptatem accusantium doloremque laudantium, totam rem aperiam, eaque ipsa quae ab illo inventore veritatis et quasi architecto beatae vitae dicta sunt explicabo. Nemo enim ipsam voluptatem quia voluptas sit aspernatur aut odit .</p>
    <div class="question">
      <svg width="48" height="48" viewBox="0 0 48 48" fill="none" stroke="#fff" stroke-width="2"><circle cx="24" cy="24" r="22"/><path d="M16 14c-2 2-2 6 2 11s9 9 12 9c2 0 4-2 4-3l-5-4-3 2c-2-1-6-5-7-7l2-3-4-5z"/></svg>
      <small>HAVE QUESTIONS?</small>
      <strong>+1 888 888 8888</strong>
    </div>
    <a class="btn" style="left:155px;top:443px;width:167px;height:39px;font-size:18px;font-weight:500">View all projects</a>
  </div>
  <div class="creek" role="img" aria-label="Aerial photograph of a winding creek through green and autumn woodland"></div>
  <svg class="abs" style="left:602px;top:258px" width="40" height="66" viewBox="0 0 40 66" fill="none" stroke="#e8e8e8" stroke-width="6"><path d="M34 4L8 33l26 29"/></svg>
  <svg class="abs" style="left:1102px;top:258px" width="40" height="66" viewBox="0 0 40 66" fill="none" stroke="#e8e8e8" stroke-width="6"><path d="M6 4l26 29L6 62"/></svg>
</section>

<footer class="footer">
  <div class="cta-strip">
    <h2>Simplifying construction.</h2>
    <a><svg width="20" height="14" viewBox="0 0 20 14" fill="none" stroke="#e2463a" stroke-width="1.6"><rect x="1" y="1" width="18" height="12"/><path d="M1 1l9 7 9-7"/></svg>Contact us</a>
  </div>
  <div class="footer-mark">VELKORA</div>

  <h6 style="left:495px">Contact us</h6>
  <div class="contact-line" style="top:248px"><svg width="12" height="16" viewBox="0 0 12 16" fill="#fff"><path d="M6 0a6 6 0 0 0-6 6c0 4 6 10 6 10s6-6 6-10a6 6 0 0 0-6-6zm0 8a2 2 0 1 1 0-4 2 2 0 0 1 0 4z"/></svg><span>482 Meridian Ave. Suite 2-118<br>Ashcombe, TN 37091</span></div>
  <div class="contact-line" style="top:300px"><svg width="13" height="13" viewBox="0 0 13 13" fill="#fff"><path d="M2 0l3 3-2 2c1 2 3 4 5 5l2-2 3 3-2 2C6 13 0 7 0 2z"/></svg><span>+1 888 888 8888</span></div>
  <div class="contact-line" style="top:337px"><svg width="14" height="11" viewBox="0 0 14 11" fill="#fff"><path d="M0 0h14v11H0zM1 1l6 5 6-5"/></svg><span>info@velkora.com</span></div>

  <h6 style="left:745px">Menu</h6>
  <ul class="menu"><li>About us</li><li>Fence &amp; gates</li><li>Commercial</li><li>Area we serve</li><li>Blog</li><li>Reviews</li><li>Contact us</li></ul>

  <h6 style="left:876px">Follow us</h6>
  <a class="quote">GET A FREE QUOTE</a>
  <hr>
  <p class="copyright">Copyright © 2025 All Rights Reserved</p>
</footer>
<div class="social" aria-label="Social media links">
  <span style="left:876px"></span><span style="left:911px"></span><span style="left:946px"></span><span style="left:981px"></span><span style="left:1016px"></span>
</div>

</body>
</html>
```